Company website for an international IT business

We require a website for our business, Korvel Solutions. The business has two primary areas: Lanterns, which includes two machine learning/deep learning based products and IT consultancy, which is the service we provide to other businesses.

We bridge cutting-edge research to market.

STYLING:
The site can be on single page or multi-page. This is fully open to suggestion. So long as the look and feel are consistent. Currently, we have no strong preference for colors, styles or layouts.
You can find the logo of our website in the attachment “Korvel-logo.png” and “Korvel-logo-landscape.png”.

CONTENT:
You can find the text of the website in “Website-Content.pdf”, which explains the services and products of our business. The format of the text is also open to suggestion - including breaking up the text into visually appealing sections.
We would also like to include suitable images on the website so that it does not appear to be a text-heavy page. We are happy to have placeholder images on stock image sites if needed. We are open to suggestions on placing of images

ATTACHMENT:

Industry/Entity Type

It Company

Coding

Coded - Design and coding required

Number of Pages Required

1 page

Colors

Designer to choose colors to be used in the design.

Requirements
Must have
• A full description of the requirement is in the attachment "Website-Content.pdf"
• The design must have HTML/CSS, and all resources relevant (images, fonts etc)
• We are
Nice to have
• We are open to suggestions on top of the requirement, please reach out and communicate.

```html
<!DOCTYPE html>
<html lang="en">
<head>
<meta charset="utf-8">
<title>Korvel Solutions</title>
<link rel="stylesheet" href="https://fonts.googleapis.com/css2?family=Lato:wght@400;700&family=Open+Sans:wght@400;600&display=swap">
<style>
:root{
  --blue:#0a7fc0;
  --blue-dark:#0868a3;
  --blue-light:#1d95d6;
  --text:#555;
  --heading:#1a1a1a;
  --gray-bg:#e8e8e8;
  --footer:#4a4a4a;
  --white:#fff;
}
*{margin:0;padding:0;box-sizing:border-box}
html,body{width:1200px;height:3651px;overflow:hidden}
body{position:relative;background:var(--white);font-family:'Open Sans',sans-serif;color:var(--text)}
.abs{position:absolute}
h1,h2,h3,.brand-name{font-family:'Lato',sans-serif}
.center{text-align:center}
.rule{position:absolute;height:3px;width:56px;background:#333;left:572px}

/* header */
.brand{left:78px;top:22px;display:flex;align-items:center;gap:14px}
.brand-mark{width:52px;height:52px;border-radius:50%;background:var(--blue)}
.brand-name{font-weight:700;font-size:24px;color:var(--heading);letter-spacing:1px}
.nav{top:42px;left:0;width:100%}
.nav a{position:absolute;font-size:17px;color:#444;text-decoration:none;text-transform:uppercase}
.nav a.active{color:var(--blue)}
.nav a.active::after{content:"";position:absolute;left:-4px;right:-4px;top:34px;height:3px;background:var(--blue)}

/* hero */
.hero-bg{top:520px;left:0}
.hero-title{left:78px;top:232px;font-size:63px;font-weight:700;color:var(--blue)}
.hero-text{left:78px;top:316px;width:440px;font-size:17px;line-height:27px}
.hero-image{left:580px;top:170px;width:540px;height:400px;border-radius:30px;transform:rotate(-8deg) skewX(-6deg);background:linear-gradient(140deg,#f3f3f3 0%,#b9bcc0 45%,#7d7f84 70%,#e6e6e6 100%);border:18px solid #fafafa;box-shadow:0 40px 50px rgba(0,0,0,.12)}

.welcome{left:183px;top:580px;width:832px;height:206px;background:var(--white);border-radius:8px;box-shadow:0 4px 14px rgba(0,0,0,.12)}
.welcome h2{position:absolute;top:40px;width:100%;font-size:33px;color:var(--blue);font-weight:700}
.welcome .rule{left:388px;top:92px}
.welcome p{position:absolute;top:112px;width:100%;font-size:15px;line-height:24px;color:#444}

.service{width:280px;text-align:center}
.service .icon{width:84px;height:84px;margin:0 auto;background:var(--white);border-radius:14px;box-shadow:0 3px 10px rgba(0,0,0,.15);display:flex;align-items:center;justify-content:center}
.service p{margin-top:34px;font-size:20px;color:var(--blue)}

/* different */
.diff-title{left:80px;top:1118px;font-size:42px;color:var(--blue);font-weight:700}
.diff-rule{left:80px;top:1188px;width:52px;height:3px;background:#333}
.diff-text{left:80px;top:1206px;width:460px;font-size:16px;line-height:26px}
.learn{left:78px;top:1340px;font-size:15px;color:var(--blue);display:flex;align-items:center;gap:8px;text-transform:uppercase}
.diff-frame{left:601px;top:1079px;width:522px;height:324px;background:var(--white);border-radius:34px;box-shadow:0 4px 16px rgba(0,0,0,.15);padding:12px 18px}
.diff-photo{width:100%;height:100%;border-radius:4px;background:linear-gradient(120deg,#cfe0ec 0%,#e8eef3 40%,#9fb8c9 70%,#dfe7ee 100%)}

/* help */
.section-title{width:100%;left:0;font-size:44px;font-weight:700;color:var(--blue);text-align:center}
.help{width:320px;text-align:center}
.help .ring{width:122px;height:122px;margin:0 auto;border-radius:50%;border:7px solid var(--blue);display:flex;align-items:center;justify-content:center}
.help p{margin-top:32px;font-size:15px;line-height:27px;color:#444}

/* agile */
.agile{top:1877px;left:0;width:1200px;height:461px;background:linear-gradient(90deg,#0b6fae 0%,#0a86c8 100%)}
.agile .col{position:absolute;top:0;height:461px;color:var(--white);text-align:center;padding:0 28px}
.agile .c1{left:480px;width:241px;background:rgba(0,40,80,.12)}
.agile .c2{left:721px;width:238px;background:rgba(0,40,80,.04)}
.agile .c3{left:959px;width:241px;background:rgba(255,255,255,.06)}
.agile h3{margin-top:144px;font-size:24px;font-weight:700}
.agile .col p{margin-top:8px;font-size:15px;line-height:27px}
.agile .col a{display:inline-block;margin-top:10px;font-size:15px;font-weight:600;color:var(--white);text-decoration:underline}
.agile-title{left:73px;top:62px;font-size:34px;font-weight:700;color:var(--white)}
.agile-ring{left:119px;top:121px}

.expertise-text{top:2474px;left:0;width:100%;font-size:16px;line-height:26px;color:#555}

/* blog */
.blog{top:2576px;left:0;width:1200px;height:711px;background:var(--gray-bg)}
.post-photo{width:321px;height:231px}
.post-card{width:278px;height:177px;background:var(--white);box-shadow:0 2px 8px rgba(0,0,0,.12);padding:22px 18px}
.post-card .meta{font-size:18px;color:#222;padding-bottom:12px;border-bottom:1px solid #ddd}
.post-card .excerpt{margin-top:10px;font-size:15px;line-height:26px;color:#666;width:180px}
.post-card .more{position:absolute;right:18px;bottom:20px;font-size:15px;color:var(--blue)}

/* footer */
.footer{top:3287px;left:0;width:1200px;height:302px;background:var(--footer);color:var(--white)}
.footer-nav{top:42px;width:100%;text-align:center;font-size:15px}
.footer-nav span{margin:0 20px}
.contact-icon{width:58px;height:58px;border-radius:50%;border:2px solid var(--white);display:flex;align-items:center;justify-content:center}
.footer-text{font-size:15px;line-height:27px;text-align:center}
.copyright{top:3589px;left:0;width:1200px;height:62px;background:var(--blue);color:var(--white);font-size:15px;text-align:center;line-height:62px}
</style>
</head>
<body>

<header>
  <div class="abs brand"><span class="brand-mark"></span><span class="brand-name">KORVEL</span></div>
  <nav class="abs nav">
    <a class="active" style="left:604px">Home</a>
    <a style="left:687px">About</a>
    <a style="left:775px">Lanterns</a>
    <a style="left:882px">Consultancy</a>
    <a style="left:1037px">Contact</a>
  </nav>
</header>

<svg class="abs hero-bg" width="1200" height="660" viewBox="0 0 1200 660" aria-hidden="true">
  <polygon points="0,80 1200,0 1200,430 0,600" fill="#ececec"/>
  <polygon points="0,80 600,40 1200,430 1200,500 0,600" fill="#f2f2f2"/>
  <polygon points="300,650 1200,300 1200,650" fill="#e4e4e4"/>
</svg>

<h1 class="abs hero-title">Korvel Solutions</h1>
<p class="abs hero-text">Lorem Ipsum is simply dummy text of the printing and typesetting industry. Lorem Ipsum has been the industry's standard dummy text</p>
<div class="abs hero-image" role="img" aria-label="Tablet showing a city skyline and a laptop at work"></div>

<section class="abs welcome center">
  <h2>Welcome to Korvel Solutions</h2>
  <span class="rule"></span>
  <p>Korvel Solutions is an IT consultancy firm with a difference<br>We can provide IT expertise for your business at any stage - from initial idea to live systems</p>
</section>

<div class="abs service" style="left:99px;top:872px">
  <div class="icon"><svg width="34" height="30" viewBox="0 0 34 30"><rect x="2" y="2" width="30" height="26" rx="3" fill="none" stroke="#0a7fc0" stroke-width="2.5"/><line x1="2" y1="9" x2="32" y2="9" stroke="#0a7fc0" stroke-width="2"/><text x="17" y="23" font-size="10" text-anchor="middle" fill="#0a7fc0" font-family="Open Sans,sans-serif">&lt;/&gt;</text></svg></div>
  <p>Software development</p>
</div>
<div class="abs service" style="left:459px;top:872px">
  <div class="icon"><svg width="36" height="36" viewBox="0 0 36 36" fill="none" stroke="#0a7fc0" stroke-width="2"><circle cx="18" cy="18" r="5"/><circle cx="18" cy="5" r="3"/><circle cx="18" cy="31" r="3"/><circle cx="5" cy="18" r="3"/><circle cx="31" cy="18" r="3"/><path d="M18 8v5M18 23v5M8 18h5M23 18h5"/></svg></div>
  <p>IOT System Design</p>
</div>
<div class="abs service" style="left:822px;top:872px">
  <div class="icon"><svg width="34" height="36" viewBox="0 0 34 36" fill="none" stroke="#0a7fc0" stroke-width="2.5"><path d="M10 33v-7c-4-3-6-7-6-11C4 8 10 3 17 3s13 5 13 12l3 6h-3v5c0 2-2 3-4 3h-4v4"/><circle cx="17" cy="15" r="4"/></svg></div>
  <p>Machine learning solutions</p>
</div>

<h2 class="abs diff-title">How are we different</h2>
<span class="abs diff-rule"></span>
<p class="abs diff-text">Lorem Ipsum is simply dummy text of the printing and typesetting industry. Lorem Ipsum has been the industry's standard dummy text ever since the 1500s, when an unknown printer took a galley of type and scrambled it to make a type specimen book.</p>
<a class="abs learn"><svg width="22" height="22" viewBox="0 0 22 22" fill="none" stroke="#555" stroke-width="1.5"><circle cx="11" cy="11" r="9"/><path d="M11 6v10M6 11h10"/></svg>Learn more</a>
<div class="abs diff-frame"><div class="diff-photo" role="img" aria-label="Team working together at laptops in a bright office"></div></div>

<h2 class="abs section-title" style="top:1474px">How can we help</h2>
<span class="rule" style="top:1541px"></span>

<div class="abs help" style="left:76px;top:1597px">
  <div class="ring"><svg width="50" height="50" viewBox="0 0 50 50" fill="none" stroke="#333" stroke-width="2"><circle cx="28" cy="27" r="14"/><path d="M28 13v-4M24 9h8M28 27l4-5M3 22h9M6 28h8M9 34h8"/></svg></div>
  <p>Acquire more development capacity<br>and get results fast</p>
</div>
<div class="abs help" style="left:439px;top:1597px">
  <div class="ring"><svg width="50" height="50" viewBox="0 0 50 50" fill="none" stroke="#333" stroke-width="2"><path d="M19 6h12l-4 8h-4zM21 14C10 20 8 30 10 38c1 4 5 6 15 6s14-2 15-6c2-8 0-18-11-24"/><text x="25" y="37" font-size="16" text-anchor="middle" fill="#333" stroke="none" font-family="Lato,sans-serif">$</text></svg></div>
  <p>Avoid the overhead incurred by frequent<br>scaling of your development team</p>
</div>
<div class="abs help" style="left:799px;top:1597px">
  <div class="ring"><svg width="54" height="40" viewBox="0 0 54 40" fill="none" stroke="#333" stroke-width="2"><path d="M0 20h10l3-6 3 12 3-18 3 24 3-28 3 30 3-24 3 18 3-10 3 6h12"/></svg></div>
  <p>Reach a wide spectrum of expertise</p>
</div>

<section class="abs agile">
  <h2 class="abs agile-title">Iterative Agile Process</h2>
  <svg class="abs agile-ring" width="240" height="240" viewBox="0 0 240 240" role="img" aria-label="Cycle diagram: Define, Build, Deliver">
    <defs>
      <path id="arcDefine" d="M27.9 153.5 A98 98 0 0 1 128.5 22.4"/>
      <path id="arcBuild" d="M145.4 25.3 A98 98 0 0 1 200.3 176.2"/>
      <path id="arcDeliver" d="M189.3 189.3 A98 98 0 0 1 35.1 169"/>
    </defs>
    <use href="#arcDefine" fill="none" stroke="#ffffff" stroke-width="38"/>
    <use href="#arcBuild" fill="none" stroke="#9a9a9a" stroke-width="38"/>
    <use href="#arcDeliver" fill="none" stroke="#3a3a3a" stroke-width="38"/>
    <g font-family="Open Sans,sans-serif" font-size="17" text-anchor="middle">
      <text dy="6" fill="#666"><textPath href="#arcDefine" startOffset="50%">1.Define</textPath></text>
      <text dy="6" fill="#fff"><textPath href="#arcBuild" startOffset="50%">2.Build</textPath></text>
      <text dy="6" fill="#fff"><textPath href="#arcDeliver" startOffset="50%">3.Deliver</textPath></text>
    </g>
  </svg>
  <div class="col c1"><h3>01. Define</h3><p>Our conversation will start with a high-level agreement on the overall strategy. Our tech team will research and investigate the context.</p><a>READ MORE</a></div>
  <div class="col c2"><h3>02. Build</h3><p>We follow a scrum methodology in our development process, that is, we carry out the work in multiple (bi-)weekly.</p><a>READ MORE</a></div>
  <div class="col c3"><h3>03. Deliver</h3><p>At the end of a contract, we ship deliverables with sufficient documentations. In addition, we will provide free support.</p><a>READ MORE</a></div>
</section>

<h2 class="abs section-title" style="top:2380px">Strong Expertise</h2>
<span class="rule" style="top:2444px"></span>
<p class="abs expertise-text center">We have many years experience in machine learning, data mining, app development,<br>DevOps and hardware design We solve "hard" problems for business</p>

<section class="abs blog">
  <h2 class="abs section-title" style="top:45px">Latest Blog</h2>
  <span class="rule" style="top:110px"></span>

  <div class="abs post-photo" style="left:78px;top:144px;background:linear-gradient(120deg,#d9a93a,#8a6a3c 60%,#c9a15a)" role="img" aria-label="Colleagues gathered around a laptop"></div>
  <div class="abs post-card" style="left:297px;top:171px"><p class="meta">posted by admin, 20/12/17</p><p class="excerpt">Lorem Ipsum is simply dummy text of the printing.</p><a class="more">Read More</a></div>

  <div class="abs post-photo" style="left:623px;top:144px;background:linear-gradient(120deg,#e8eef2,#8f9aa4 50%,#d6dde2)" role="img" aria-label="Business meeting at an office table"></div>
  <div class="abs post-card" style="left:842px;top:171px"><p class="meta">posted by admin, 20/12/17</p><p class="excerpt">Lorem Ipsum is simply dummy text of the printing.</p><a class="more">Read More</a></div>

  <div class="abs post-photo" style="left:78px;top:417px;background:linear-gradient(180deg,#2d3a46,#c9cfd2 55%,#3b3f44)" role="img" aria-label="Silhouettes of a team against a bright window"></div>
  <div class="abs post-card" style="left:297px;top:443px"><p class="meta">posted by admin, 20/12/17</p><p class="excerpt">Lorem Ipsum is simply dummy text of the printing.</p><a class="more">Read More</a></div>

  <div class="abs post-photo" style="left:623px;top:417px;background:linear-gradient(160deg,#24426b,#5d7fa8 50%,#c7d0da)" role="img" aria-label="Handshake in front of a city skyline"></div>
  <div class="abs post-card" style="left:842px;top:443px"><p class="meta">posted by admin, 20/12/17</p><p class="excerpt">Lorem Ipsum is simply dummy text of the printing.</p><a class="more">Read More</a></div>
</section>

<footer class="abs footer">
  <p class="abs footer-nav"><span>Home</span><span>About</span><span>Lanterns</span><span>Consultancy</span><span>Contact</span></p>
  <svg class="abs" style="left:415px;top:147px" width="390" height="14" viewBox="0 0 390 14" aria-hidden="true">
    <line x1="6" y1="7" x2="384" y2="7" stroke="#fff" stroke-width="1.5"/>
    <circle cx="6" cy="7" r="4" fill="#4a4a4a" stroke="#fff" stroke-width="2"/>
    <circle cx="384" cy="7" r="4" fill="#4a4a4a" stroke="#fff" stroke-width="2"/>
  </svg>
  <div class="abs contact-icon" style="left:280px;top:125px"><svg width="24" height="24" viewBox="0 0 24 24" fill="#fff"><path d="M6.6 10.8a15 15 0 0 0 6.6 6.6l2.2-2.2c.3-.3.7-.4 1-.2 1.1.4 2.3.6 3.6.6.6 0 1 .4 1 1V20c0 .6-.4 1-1 1A17 17 0 0 1 3 4c0-.6.4-1 1-1h3.5c.6 0 1 .4 1 1 0 1.3.2 2.5.6 3.6.1.3 0 .7-.2 1z"/></svg></div>
  <div class="abs contact-icon" style="left:577px;top:125px;background:#4a4a4a"><svg width="22" height="26" viewBox="0 0 22 26" fill="#fff"><path d="M11 1C5.5 1 2 5 2 10c0 6 9 15 9 15s9-9 9-15c0-5-3.5-9-9-9zm0 12.5a3.5 3.5 0 1 1 0-7 3.5 3.5 0 0 1 0 7z"/></svg></div>
  <div class="abs contact-icon" style="left:882px;top:125px"><svg width="24" height="18" viewBox="0 0 24 18" fill="none" stroke="#fff" stroke-width="2"><rect x="1" y="1" width="22" height="16" rx="2"/><path d="M1 2l11 8 11-8"/></svg></div>
  <p class="abs footer-text" style="left:229px;top:197px;width:160px">123 456 7890</p>
  <p class="abs footer-text" style="left:450px;top:197px;width:312px">Lorem Ipsum is simply dummy text<br>of the printing and typesetting.</p>
  <p class="abs footer-text" style="left:831px;top:197px;width:160px">info@korvel.com</p>
</footer>

<p class="abs copyright">2018 ©KORVEL. All Rights Reserved.</p>

</body>
</html>
```